Thornbury Spa

We are a large Miami Beach spa and salon. I am still building our website but you can use it as a resource to gain a better understanding of who we are ....www.velloraspa-studio.com.

We offer a comprehensive list of services in hair, nails, massage, skin care, tanning, spray tanning and waxing and we offer high quality products for skin care, tanning and hair. We are open 7 days.

We would like to see a clean and simple menu that looks a lot like the one from "The Spa at Larkwood." In particular, we have a copy of a menu from their West Hollywood, CA location that is just beautiful. In the uploaded content you will see a sampling of that menu. We would like to see greys, blacks, silvers, whites and warm colors like reds and oranges. We specifically attempt to remain gender neutral so that we don't attract only girls (with pink colors and flowers etc). The final design should convey a simple, clean, friendly environment and the final product should be sized such that it is 1.) portable and 2.) inexpensive to print. We will be running thousands of these at a time so cost of printing is a consideration.

The booklet consists of two parts: one part is the standard menu with descriptions of services and products and photos etc (think of this as the sales piece that convinces a potential customer to visit) and will be stapled together like you would expect a small menu to be and should resemble the Larkwood menu. The prices should not be included in this part of the booklet that will be printed and stapled. The other part is a single insert and is removable and replaceable. I want this removable insert placed in the last page of the book in a folder pocket or something else that you can think of so that when it's time to change prices here that I am not throwing away all of the booklets....I am only replacing the inserts at the end of the menu booklet. Please design this single page insert so that should a customer remove it from the booklet and keep it, that it stands alone with our name, logo, website and phone number. This page can and probably will have to be 2 sided.

At the back of the booklet, I also want the polices to be printed in one page (think fine print in any sort of business dealing.)

With regard to the look and feel slider of economical v upmarket...we definitely want to convey we deliver upmarket services at reasonable prices. Think, world class services and products at reasonable, everyday prices.

With regard to the uploaded files:
I uploaded both EPS and TIF formats. The colors in those files are not the palette we want at all. The colors we want use for the circular logo must match the standard colors as depicted in the uploaded file "Thornburytanrooms"

Target Market(s)

The target market is the average 20-35 year old in Miami Beach that cares about their appearance. The range of clientele is quite diverse.

Industry/Entity Type

Environment

Requirements
Must have
• It must have elegant and simple photographs that relate to the services being offered. We are selling a service set and an environment...so this menu should be reflect that goal. The logo should be repeated often throughout the book but in subtle ways.

Stock photos are fine as long as they don't seem obviously stock.

Should not have
• Nothing buddha like. Nothing themed. It should be all inclusive and not seek to identify with any particular group or gender.

Nothing that fits the stereotype of "Miami Beach." We want to represent ourselves in the same category as the best spas in the world because we moving everything we do in that direction. Think class!

```html
<!DOCTYPE html>
<html lang="en">
<head>
<meta charset="utf-8">
<title>Thornbury Spa — Massage Menu Spread</title>
<link href="https://fonts.googleapis.com/css2?family=Source+Sans+3:wght@300;400;600&display=swap" rel="stylesheet">
<style>
  :root {
    --ink-black: #000000;
    --paper-white: #ffffff;
    --text-light: #f4f4f4;
    --frame-grey: #8e8e8e;
    --title-grey: #6b6b6b;
    --band-tint: rgba(250, 236, 226, 0.74);
    --photo-window: #f7f6f4;
    --photo-linen: #ece8e4;
    --photo-skin: rgba(214, 178, 152, 0.55);
    --photo-shade: rgba(40, 34, 33, 0.55);
    --brand-tone: #b7ad86;
  }
  * { margin: 0; padding: 0; box-sizing: border-box; }
  html, body {
    width: 1200px; height: 600px; overflow: hidden;
    background: var(--paper-white);
    font-family: "Source Sans 3", "Helvetica Neue", Arial, sans-serif;
  }
  .spread { position: relative; width: 1200px; height: 600px; overflow: hidden; }

  .service-panel {
    position: absolute; left: 540px; top: 0; width: 660px; height: 600px;
    background: var(--ink-black);
  }

  .feature-photo {
    position: absolute; left: 0; top: 0; width: 664px; height: 600px;
    border-bottom-right-radius: 113px 167px;
    overflow: hidden;
    background:
      radial-gradient(ellipse 260px 230px at 340px 110px, var(--photo-shade) 0%, rgba(40, 34, 33, 0.25) 45%, transparent 80%),
      radial-gradient(ellipse 340px 190px at 360px 400px, var(--photo-skin) 0%, transparent 80%),
      radial-gradient(ellipse 200px 160px at 200px 190px, rgba(220, 190, 165, 0.35) 0%, transparent 80%),
      linear-gradient(100deg, var(--photo-linen) 0%, #f1ede9 35%, var(--photo-window) 100%);
  }
  .title-band {
    position: absolute; left: 0; top: 433px; width: 100%; height: 106px;
    background: var(--band-tint);
  }
  .section-title {
    position: absolute; left: 30px; top: 464px;
    font-weight: 300; font-size: 42px; letter-spacing: 10px;
    color: var(--title-grey); line-height: 1;
  }
  .section-intro {
    position: absolute; left: 318px; top: 466px; width: 280px;
    font-size: 8px; letter-spacing: 1.1px; line-height: 10.5px;
    color: #2c2c2c; font-weight: 400;
  }

  .page-frame {
    position: absolute; left: 18px; top: 18px; width: 1164px; height: 561px;
    border: 2px solid var(--frame-grey);
    pointer-events: none;
  }

  .service-list {
    position: absolute; left: 708px; top: 0; width: 440px; height: 600px;
    color: var(--text-light);
  }
  .service-head, .price-row {
    position: absolute; left: 0; width: 440px;
    display: grid; grid-template-columns: 262px 76px 1fr;
    line-height: 16px;
  }
  .service-head { font-size: 12px; font-weight: 400; }
  .service-name { text-transform: uppercase; }
  .service-desc {
    position: absolute; left: 0; width: 433px;
    font-size: 10px; line-height: 16.7px; font-weight: 400;
  }
  .price-row { font-size: 10px; font-weight: 600; }

  .prenatal-head { top: 63px; }
  .prenatal-desc { top: 97px; }
  .prenatal-price { top: 214px; }
  .reflex-head { top: 280px; }
  .reflex-desc { top: 315px; }
  .reflex-price { top: 465px; }

  .brand-mark {
    position: absolute; left: 1030px; top: 524px; width: 136px; height: 68px;
    background: var(--ink-black);
    display: flex; flex-direction: column; align-items: center; justify-content: center; gap: 5px;
    color: var(--brand-tone);
  }
  .brand-dot {
    width: 20px; height: 20px; border-radius: 50%;
    background: var(--brand-tone);
  }
  .brand-name {
    font-size: 15px; font-weight: 400; letter-spacing: 1.5px; text-transform: uppercase;
    white-space: nowrap;
  }
</style>
</head>
<body>
<div class="spread">
  <div class="service-panel"></div>

  <div class="feature-photo" role="img" aria-label="Photograph of a therapist giving a prenatal massage to an expectant mother resting on white pillows in a bright room">
    <div class="title-band"></div>
    <h1 class="section-title">MASSAGE</h1>
    <p class="section-intro">Unwind in a calm room where skilled hands ease tension, restore balance and leave you rested. Every session is shaped around your body, your pace and the quiet you came for.</p>
  </div>

  <div class="page-frame"></div>

  <section class="service-list">
    <div class="service-head prenatal-head">
      <span class="service-name">Prenatal Massage</span>
      <span>Residents</span>
      <span>Hotel Guests</span>
    </div>
    <p class="service-desc prenatal-desc">As your pregnancy advances, your growing belly can place extra stress on your muscles and impede normal circulation. Our unique approach is designed to address your pregnancy needs and any aches and pains that may accompany it- with special attention to areas such as your lower back, buttocks and hips. By gently manipulating your skin through slow, kneading movements, our therapists will work to relieve stress and soothe sore muscles. Note: Expectant mother must be at least 20 weeks.</p>
    <div class="price-row prenatal-price">
      <span>The 60-Minute Prenatal Massage</span>
      <span>$99.00</span>
      <span>$115.00</span>
    </div>

    <div class="service-head reflex-head">
      <span class="service-name">Reflexology</span>
      <span></span>
      <span></span>
    </div>
    <p class="service-desc reflex-desc">An ancient practice first noted in hieroglyphic references in a physician's tomb at Saqqara in ancient Egypt, reflexology is an alternative health treatment that utilizes and encourages the body's natural capacity to heal itself, by applying pressure to specific points on the feet, hands and ears called reflex points. Reflexology treatments are administered by applying direct physical pressure to the reflex points of the hands and feet with either finger, thumb or hand techniques. No oils or lotions are required in the treatment. Reflex points that exhibit blockages in energy flow normally feel bruised at best and painful at worst. Stimulating these reflexes properly can help many health problems in a natural way.</p>
    <div class="price-row reflex-price">
      <span>The 45 Minute Reflexology Session</span>
      <span>$100.00</span>
      <span>$115.00</span>
    </div>
  </section>

  <div class="brand-mark">
    <span class="brand-dot"></span>
    <span class="brand-name">Thornbury Spa</span>
  </div>
</div>
</body>
</html>
```